Business Card Design

New business card design

Target Market(s)

Residential & Commercial Property Managers

Industry/Entity Type

Plumbing Services

Contact Information for Business Card

Name - Rowan Keddle, title - Director, Phone Number - 0431 286 517, email - rowan@tbk-plumbing.com.au, Company ABN - 73 215 904 386,

Font styles to use
Sans Serif

Colors
0054AA
0677BA
7BADD7
CADEEF
E8F1F8

```html
<!DOCTYPE html>
<html lang="en">
<head>
<meta charset="utf-8">
<title>TBK Plumbing Services – Business Card</title>
<link href="https://fonts.googleapis.com/css2?family=Montserrat:wght@400;500;700&display=swap" rel="stylesheet">
<style>
  :root {
    --page: #9c9c9c;
    --card: #1d222a;
    --blue: #29a8e0;
    --white: #ffffff;
    --text: #f2f4f6;
    --muted: #5b5550;
  }
  * { margin: 0; padding: 0; box-sizing: border-box; }
  html, body { width: 1093px; height: 1200px; overflow: hidden; }
  body {
    background: var(--page);
    font-family: "Montserrat", Arial, sans-serif;
    position: relative;
  }
  .card {
    position: absolute;
    left: 270px;
    width: 575px;
    height: 358px;
    background: var(--card);
    border-radius: 20px;
    box-shadow: -5px 5px 0 var(--blue), 0 8px 14px rgba(0,0,0,0.45);
    color: var(--text);
  }
  .card--front { top: 225px; }
  .card--back { top: 615px; height: 362px; }

  .brand {
    position: absolute;
    left: 30px;
    top: 30px;
    font-weight: 500;
    color: var(--white);
    font-size: 40px;
    letter-spacing: 2px;
    line-height: 1;
  }
  .brand__tag {
    display: block;
    margin-top: 14px;
    font-size: 8px;
    letter-spacing: 8px;
    color: var(--white);
    opacity: 0.35;
  }
  .holder {
    position: absolute;
    right: 35px;
    top: 38px;
    text-align: right;
  }
  .holder__name { font-weight: 700; font-size: 21px; color: var(--blue); line-height: 1.1; }
  .holder__title { font-size: 13px; color: var(--text); margin-top: 3px; }

  .address {
    position: absolute;
    left: 30px;
    top: 177px;
    font-size: 13.5px;
    line-height: 16px;
  }
  .contacts {
    position: absolute;
    left: 30px;
    top: 234px;
    list-style: none;
    font-size: 13px;
  }
  .contacts li {
    display: flex;
    align-items: center;
    height: 25px;
  }
  .contacts svg { width: 13px; height: 13px; margin-right: 9px; fill: var(--blue); }
  .abn { position: absolute; left: 30px; top: 315px; font-size: 13px; }
  .abn__label { color: var(--blue); font-weight: 700; }

  .drop-area {
    position: absolute;
    left: 390px;
    top: 195px;
    width: 150px;
    height: 150px;
    border-radius: 50%;
    background: var(--blue);
  }

  .brand--center {
    left: 0;
    right: 0;
    top: 135px;
    text-align: center;
    font-size: 66px;
    letter-spacing: 4px;
  }
  .brand--center .brand__tag {
    font-size: 12px;
    letter-spacing: 14px;
    margin-top: 26px;
    color: var(--muted);
    opacity: 1;
  }
</style>
</head>
<body>
  <section class="card card--front">
    <div class="brand">tbk<span class="brand__tag">plumbing services</span></div>

    <div class="holder">
      <div class="holder__name">Rowan Keddle</div>
      <div class="holder__title">Director</div>
    </div>

    <p class="address">48 Cedar Bend Road<br>Fairview, TN 37062</p>

    <ul class="contacts">
      <li>
        <svg viewBox="0 0 24 24" aria-hidden="true"><path d="M6.6 10.8c1.4 2.8 3.8 5.1 6.6 6.6l2.2-2.2c.3-.3.7-.4 1-.2 1.1.4 2.3.6 3.6.6.6 0 1 .4 1 1V20c0 .6-.4 1-1 1C10.6 21 3 13.4 3 4c0-.6.4-1 1-1h3.5c.6 0 1 .4 1 1 0 1.3.2 2.5.6 3.6.1.3 0 .7-.2 1z"/></svg>
        0431 286 517
      </li>
      <li>
        <svg viewBox="0 0 24 24" aria-hidden="true"><path d="M2 5h20v14H2z M2 5l10 7 10-7" /><path d="M2 6l10 7 10-7" fill="#1d222a"/></svg>
        rowan@tbk-plumbing.com.au
      </li>
      <li>
        <svg viewBox="0 0 24 24" aria-hidden="true"><circle cx="12" cy="12" r="10"/><path d="M7 6c2 1 3 3 2 5s1 3 0 5M15 4c-1 2 1 3 3 4M14 14c2 0 3 2 2 4" stroke="#1d222a" stroke-width="1.6" fill="none"/></svg>
        www.tbk-plumbing.com.au
      </li>
    </ul>

    <p class="abn"><span class="abn__label">ABN</span> - 73 215 904 386</p>

    <div class="drop-area" role="img" aria-label="Large brand symbol decoration"></div>
  </section>

  <section class="card card--back">
    <div class="brand brand--center">tbk<span class="brand__tag">plumbing services</span></div>
  </section>
</body>
</html>
```